South Florida Real Estate Brokerage Business

The name is LAKE VORISSA REAL ESTATE.
The company is a Real estate realty based in Miami.
Is targeted to Latin American clients.
Must express luxury, and efficiency.
Target clients for properties around 250k to a million +.
Vorissa means Royal in Latin.
Should communicate safety and knowledge of the product and transaction with a tech edge.

The web design needs to be a Social tool, with Friendloop and other media integration of some sort. Needs to have a Show case place, a Search place (MLS listings) with maps and filters.
Needs to reflect luxury but also mixed with a social edge capable of engaging clients or transition them to communicate with the page.
Include the logo from the uploaded files, feel free to change the color or font per webdesign.
This is a Front en design, layout and graphics.
Possible future programming if approved.
I can receive Quotes for the Code part.

Spanish and English speakers living in Latin America and Canada looking for apartments and houses to buy.

Business

• Search area.
Neighbourhood area.
Could be a blog or news area.
Client registration.
Social Plugin
• Social linking to networks.
Log in with friendloop account.
Friendloop Like.

```html
<!DOCTYPE html>
<html lang="en">
<head>
<meta charset="utf-8">
<title>Lake Vorissa Real Estate</title>
<link rel="stylesheet" href="https://fonts.googleapis.com/css2?family=Cinzel:wght@400&family=Libre+Baskerville&family=Lato:wght@300;400&family=Oswald:wght@500&family=PT+Sans:ital,wght@0,400;0,700;1,400&display=swap">
<style>
:root{
  --ink-dark:#1d1d1d;
  --ink-deep:#141414;
  --gold:#c6913f;
  --gold-light:#e0b56e;
  --gold-dark:#a8742c;
  --gold-text:#c9a25c;
  --sand:#ece3d2;
  --sand-soft:#f3efe6;
  --panel:#f7f3ec;
  --page:#efefef;
  --white:#fff;
  --text:#222;
  --muted:#777;
  --line:#d9d2c4;
}
*{box-sizing:border-box;margin:0;padding:0}
html,body{width:1000px;height:1200px;overflow:hidden}
body{position:relative;background:var(--page);font-family:"PT Sans",sans-serif;color:var(--text);font-size:11px}
.abs{position:absolute}
.top-band{left:0;top:0;width:1000px;height:480px;background:linear-gradient(#222,#1a1a1a)}
.footer-band{left:0;top:994px;width:1000px;height:156px;background:var(--gold)}
.bottom-band{left:0;top:1150px;width:1000px;height:50px;background:var(--ink-deep)}

.logo{left:130px;top:38px;width:185px;text-align:center;font-family:"Cinzel",serif;color:var(--gold-text);font-size:21px;line-height:26px;letter-spacing:1px}
.logo-mark{display:block;margin:0 auto 6px;width:14px;height:14px;background:var(--gold-text)}

.login-title{left:573px;top:18px;color:var(--gold-text);font-size:12px;letter-spacing:.3px}
.login-field{top:38px;width:132px;height:20px;background:#fff;border:1px solid #bbb;font-size:10px;color:#444;padding:3px 6px}
.login-btn{left:847px;top:38px;width:43px;height:20px;border-radius:3px;background:linear-gradient(var(--gold-light),var(--gold-dark));color:#2a1a05;font-size:11px;text-align:center;line-height:20px}
.login-help{left:575px;top:61px;color:#999;font-size:10px}

.frame{left:100px;top:131px;width:800px;height:880px;background:var(--white);box-shadow:0 2px 4px rgba(0,0,0,.2)}
.swoop{left:100px;top:0;width:800px;height:160px}
.nav{left:370px;top:93px;width:530px;height:38px;background:linear-gradient(var(--gold-light),var(--gold-dark));display:flex}
.nav a{display:block;flex:none;white-space:nowrap;text-align:center;color:#fff;text-decoration:none;font-size:13px;line-height:38px;border-left:1px solid rgba(255,255,255,.3);text-shadow:0 1px 1px rgba(0,0,0,.3)}
.nav a:first-child{border-left:none}

.hero{left:109px;top:141px;width:782px;height:339px;background:linear-gradient(#bcd0e6 0%,#d8d4c4 35%,#c8b48e 55%,#6f8a4a 80%,#4f7a32 100%)}
.hero-arrow{top:286px;width:50px;height:50px;border-radius:50%;background:#fff;box-shadow:0 1px 3px rgba(0,0,0,.3)}
.hero-arrow svg{position:absolute;top:15px;width:20px;height:20px}

.welcome{left:109px;top:487px;width:783px;height:200px;background:var(--sand)}
.welcome h1{position:absolute;left:18px;top:11px;font-weight:400}
.welcome .w1{display:block;font-family:"Lato",sans-serif;font-weight:300;font-size:26px;color:#333}
.welcome .w2{display:block;font-family:"Libre Baskerville",serif;font-size:22px;color:#333;margin-top:2px}
.welcome p{position:absolute;left:18px;top:81px;width:345px;font-size:10.3px;line-height:16.2px;color:#222}

.search-tab{left:510px;top:424px;width:172px;height:33px;background:var(--sand);border:2px solid var(--gold);border-bottom:none;font-size:16px;color:#3a2a10;padding:6px 7px;letter-spacing:.2px;white-space:nowrap}
.search{left:502px;top:456px;width:381px;height:215px;background:var(--panel);border:2px solid #fff;box-shadow:0 2px 10px rgba(0,0,0,.25)}
.quick{position:absolute;left:0;top:0;width:377px;height:52px;background:var(--sand)}
.quick-label{position:absolute;left:12px;top:9px;font-size:14px;line-height:16px;text-align:center;color:#222;padding-right:10px;border-right:1px solid var(--line)}
.quick-cap{position:absolute;left:85px;top:7px;font-size:12px}
.input{position:absolute;height:22px;background:#fff;border:1px solid var(--line)}
.select{position:absolute;height:22px;background:#fff;border:1px solid var(--line);font-size:10px;color:#555;padding:4px 8px}
.select::after{content:"";position:absolute;right:0;top:0;width:20px;height:20px;background:linear-gradient(#e2c38c,#c9a062)}
.select i{position:absolute;right:5px;top:8px;border:5px solid transparent;border-top-color:#fff;z-index:1}
.go{position:absolute;left:338px;top:19px;width:31px;height:25px;border-radius:3px;background:linear-gradient(var(--gold-light),var(--gold-dark));color:#fff;font-size:11px;font-weight:700;text-align:center;line-height:25px}
.lbl{position:absolute;font-size:12px;color:#222}
.btn{position:absolute;top:169px;height:27px;border-radius:4px;background:linear-gradient(#dcb46c,#b8832f);color:#fff;font-size:11.5px;font-weight:700;line-height:27px;text-align:center;white-space:nowrap;box-shadow:0 1px 2px rgba(0,0,0,.3)}
.adv{position:absolute;left:280px;top:176px;color:#a77a33;font-size:10.5px;font-weight:700;white-space:nowrap}

.news{left:109px;top:696px;width:223px;height:306px;background:var(--sand-soft)}
.col-title{position:absolute;font-size:17px;color:#111;white-space:nowrap}
.view-all{position:absolute;left:161px;top:18px;font-size:9px;color:#888}
.news-item{position:absolute;left:16px;width:191px;border-top:1px solid var(--line);padding-top:12px}
.date{position:absolute;left:1px;width:46px;height:46px;border-radius:50%;background:var(--sand);text-align:center;font-size:10px;color:#333;line-height:11px;padding-top:5px}
.date b{display:block;font-size:14px;line-height:15px;font-weight:700}
.news-text{margin-left:60px;font-size:10px;line-height:13px;color:#333}
.news-text strong{display:block;color:#3a2a10;margin-bottom:2px}

.feature-photo{left:367px;top:765px;width:190px;height:140px;background:linear-gradient(#a8c3e8,#e8ecef 45%,#9aa08e 75%,#4f7035);border:3px solid #fff;box-shadow:0 2px 6px rgba(0,0,0,.3)}
.feature-back{left:362px;top:754px;width:196px;height:158px;background:#e6eee0;transform:rotate(-3deg)}
.ring{width:26px;height:26px;border-radius:50%;background:var(--sand);top:820px}
.ring svg{position:absolute;left:8px;top:7px;width:10px;height:12px}
.feature-text{left:363px;top:931px;width:200px;font-size:10.5px;line-height:16px}
.divider{left:596px;top:725px;width:1px;height:275px;background:#ddd}

.map{left:617px;top:750px;width:145px;height:92px;background:linear-gradient(135deg,#f0e0b0,#e5cf95)}
.map-text{left:771px;top:749px;width:104px;font-size:10.2px;line-height:15px}
.testi{left:616px;top:870px;width:264px;height:125px;background:linear-gradient(#ececec,#fafafa)}
.testi h3{position:absolute;left:12px;top:14px;font-weight:400;font-size:19px;color:#333}
.testi p{position:absolute;left:14px;top:46px;width:234px;font-style:italic;color:#666;font-size:10.5px;line-height:15px}
.testi .by{position:absolute;right:16px;top:96px;text-align:right;font-size:10.5px;line-height:14px}
.testi .by i{color:#666}

.f-title{font-size:14px;color:#1a1a1a}
.f-links{left:104px;top:1056px;width:180px;display:grid;grid-template-columns:110px 70px;row-gap:6px;color:#fff;font-size:10px}
.mail-title{left:303px;top:1034px;height:25px;background:#111;color:#fff;font-family:"Oswald",sans-serif;font-size:18px;line-height:25px;padding:0 4px;letter-spacing:.3px;white-space:nowrap}
.mail-text{left:303px;top:1070px;width:150px;color:#fff;font-size:11px;line-height:14px}
.mail-input{left:303px;top:1111px;width:174px;height:22px;border-radius:11px;background:#fff;font-size:10px;color:#444;padding:4px 8px}
.mail-join{left:445px;top:1111px;width:32px;height:22px;border-radius:11px;background:#e86a1e;color:#fff;font-size:10px;text-align:center;line-height:22px;font-family:"Oswald",sans-serif}
.blog{left:522px;top:1031px;width:190px;color:#fff;font-size:10px;line-height:13px}
.blog .d{color:#f3ddb4;font-size:9px;letter-spacing:.5px;margin-top:5px}
.blog strong{display:block}
.social{left:737px;top:1058px;width:160px;display:grid;grid-template-columns:80px 80px;row-gap:3px;color:#fff;font-size:10px;line-height:12px}
.social span{display:flex;align-items:center;gap:4px;white-space:nowrap}
.social i{display:inline-block;width:10px;height:10px;background:#fff}
.plus{left:737px;top:1091px;display:flex;gap:4px;align-items:center;font-size:9px}
.plus .box{width:26px;height:14px;background:#e8e8e8;border:1px solid #999}
.plus .count{background:#fff;border:1px solid #aaa;padding:0 4px}
.like{left:737px;top:1116px;display:flex;gap:5px;align-items:center;font-size:9.5px;color:#fff;white-space:nowrap}
.like .btn-like{background:#eceef5;border:1px solid #cad4e7;color:#3b5998;font-weight:700;padding:1px 5px;border-radius:2px}

.foot-logo{left:96px;top:1160px;width:66px;font-family:"Cinzel",serif;color:var(--gold-text);font-size:9px;line-height:11px;text-align:center}
.legal{left:175px;top:1166px;color:#888;font-size:10px}
.copy{left:175px;top:1181px;color:#ddd;font-size:10px}
</style>
</head>
<body>
<div class="abs top-band"></div>
<div class="abs footer-band"></div>
<div class="abs bottom-band"></div>

<div class="abs frame"></div>
<svg class="abs swoop" viewBox="0 0 800 160" aria-hidden="true">
  <path d="M0 0 H440 C420 40 330 50 300 70 C260 95 230 110 160 100 C90 90 40 130 0 132 Z" fill="#1d1d1d"/>
</svg>

<div class="abs logo"><span class="logo-mark"></span>LAKE VORISSA<br>REAL ESTATE</div>

<div class="abs login-title">CLIENT LOGIN</div>
<div class="abs login-field" style="left:573px">Username</div>
<div class="abs login-field" style="left:709px">Password</div>
<div class="abs login-btn">LOGIN</div>
<div class="abs login-help">Forgot your password? / Register</div>

<nav class="abs nav">
  <a href="#" style="width:52px">Home</a><a href="#" style="width:72px">Company</a><a href="#" style="width:80px">Associates</a><a href="#" style="width:116px">Search Properties</a><a href="#" style="width:140px">Marketing and Design</a><a href="#" style="width:70px">Contact</a>
</nav>

<div class="abs hero" role="img" aria-label="Photo of a two-storey suburban family house with a porch, lawn and trees"></div>
<div class="abs hero-arrow" style="left:85px"><svg viewBox="0 0 20 20" style="left:18px"><path d="M14 2 L5 10 L14 18" stroke="#111" stroke-width="4" fill="none"/></svg></div>
<div class="abs hero-arrow" style="left:868px"><svg viewBox="0 0 20 20" style="left:12px"><path d="M6 2 L15 10 L6 18" stroke="#111" stroke-width="4" fill="none"/></svg></div>

<section class="abs welcome">
  <h1><span class="w1">Welcome to</span><span class="w2">Lake Vorissa Real Estate</span></h1>
  <p>Lorem ipsum dolor sit amet, consectetur adipisicing elit, sed do eiusmod tempor incididunt ut labore et dolore magna aliqua. Ut enim ad minim veniam, quis nostrud exercitation ullamco laboris nisi ut aliquip ex ea commodo consequat. Duis aute irure dolor in reprehenderit in voluptate velit esse cillum dolore eu fugiat nulla pariatur. Excepteur sint occaecat cupidatat non proident, sunt in culpa qui officia deserunt mollit anim id est laborum.</p>
</section>

<div class="abs search-tab">PROPERTYES SEARCH</div>
<section class="abs search">
  <div class="quick">
    <div class="quick-label">QUICK<br>SEARCH</div>
    <div class="quick-cap">MLS # or Street Name</div>
    <div class="input" style="left:84px;top:24px;width:245px"></div>
    <div class="go">GO</div>
  </div>
  <div class="lbl" style="left:18px;top:56px">City</div>
  <div class="input" style="left:18px;top:76px;width:165px"></div>
  <div class="lbl" style="left:200px;top:56px">Location</div>
  <div class="select" style="left:200px;top:76px;width:163px">Any<i></i></div>
  <div class="lbl" style="left:18px;top:109px">Price</div>
  <div class="select" style="left:18px;top:130px;width:78px">Any<i></i></div>
  <div class="lbl" style="left:101px;top:134px;font-size:10px">to</div>
  <div class="select" style="left:113px;top:130px;width:78px">Any<i></i></div>
  <div class="lbl" style="left:200px;top:109px">Beds</div>
  <div class="select" style="left:200px;top:130px;width:78px">Any<i></i></div>
  <div class="lbl" style="left:285px;top:109px">Baths</div>
  <div class="select" style="left:285px;top:130px;width:78px">Any<i></i></div>
  <div class="btn" style="left:20px;width:119px">PROPERTY SEARCH</div>
  <div class="btn" style="left:152px;width:116px">SEARCH BY MLS #</div>
  <div class="adv">Advanced Search</div>
</section>

<section class="abs news">
  <h2 class="col-title" style="left:16px;top:14px;font-weight:400">News</h2>
  <div class="view-all">VIEW ALL ▸</div>
  <div class="news-item" style="top:39px"><div class="date"><b>31</b>Oct<br>2011</div><div class="news-text"><strong>Lorem ipsum dolor sit</strong>Lorem ipsum dolor sit amet, consectetur adipisicing elit, sed do eiusmod tempor incididunt</div></div>
  <div class="news-item" style="top:126px"><div class="date"><b>31</b>Oct<br>2011</div><div class="news-text"><strong>Lorem ipsum dolor sit</strong>Lorem ipsum dolor sit amet, consectetur adipisicing elit, sed do eiusmod tempor incididunt</div></div>
  <div class="news-item" style="top:214px"><div class="date"><b>31</b>Oct<br>2011</div><div class="news-text"><strong>Lorem ipsum dolor sit</strong>Lorem ipsum dolor sit amet, consectetur adipisicing elit, sed do eiusmod tempor incididunt</div></div>
</section>

<h2 class="abs col-title" style="left:354px;top:710px;font-weight:400">Feature Property</h2>
<div class="abs feature-back"></div>
<div class="abs feature-photo" role="img" aria-label="Photo of a white house with a covered porch and dormer windows"></div>
<div class="abs ring" style="left:342px"><svg viewBox="0 0 10 12"><path d="M8 1 L2 6 L8 11" stroke="#333" stroke-width="1.6" fill="none"/></svg></div>
<div class="abs ring" style="left:554px"><svg viewBox="0 0 10 12"><path d="M2 1 L8 6 L2 11" stroke="#333" stroke-width="1.6" fill="none"/></svg></div>
<p class="abs feature-text">Lorem ipsum dolor sit amet, consectetur adipisicing elit, sed do eiusmod tempor incididunt ut labore et dolore.</p>
<div class="abs divider"></div>

<h2 class="abs col-title" style="left:620px;top:710px;font-weight:400">Neighbourhood area</h2>
<div class="abs map" role="img" aria-label="Map of the United States showing neighbourhood areas"></div>
<p class="abs map-text">Lorem ipsum dolor sit amet, consectetur adipisicing elit, sed do eiusmod tempor incididunt ut labore et dolore magna aliqua.</p>

<section class="abs testi">
  <h3>Testimonials</h3>
  <p>Lorem ipsum dolor sit amet, consectetur adipisicing elit, sed do eiusmod tempor incididunt ut labore et dolore magna</p>
  <div class="by"><strong>Lorem ipsum</strong><br><i>dolor sit</i></div>
</section>

<h3 class="abs f-title" style="left:101px;top:1031px;font-weight:400">Quick Links</h3>
<div class="abs f-links"><span>Home</span><span>BLog</span><span>About Us</span><span>Testimonials</span><span>Search Properties</span><span>Contact</span><span>News</span></div>

<div class="abs mail-title">JOIN OUR MAILING LIST</div>
<p class="abs mail-text">Sign up for our e-mail list to receive updates</p>
<div class="abs mail-input">Your e-mail address</div>
<div class="abs mail-join">JOIN</div>

<div class="abs blog">
  <h3 class="f-title" style="font-weight:400;margin-bottom:4px">Blog</h3>
  <div class="d">09 April 2012</div><strong>Lorem ipsum dolor sit amet, consectetur adipisicing elit, sed do</strong>
  <div class="d" style="margin-top:8px">06 April 2012</div><strong>Lorem ipsum dolor sit amet, consectetur adipisicing elit, sed do</strong>
</div>

<h3 class="abs f-title" style="left:735px;top:1031px;font-weight:400">Connect With Us</h3>
<div class="abs social"><span><i></i>Friendloop</span><span><i></i>Chirpwave</span><span><i></i>Linkforge</span><span><i></i>RSS</span></div>
<div class="abs plus"><span class="box"></span><span class="count">17</span></div>
<div class="abs like"><span class="btn-like">Like</span><span>2,942 people like this.</span></div>

<div class="abs foot-logo">LAKE VORISSA REAL ESTATE</div>
<div class="abs legal">Terms of Use | Privacy Policy</div>
<div class="abs copy">© 2011 Lake Vorissa Real Estate .All Rights Reserved</div>
</body>
</html>
```